How likely are people to engage in social distancing? We need a good illustration to show the data!

We surveyed U.S. adults March 20th - 24th, 2020 and asked how likely they were to engage in social distancing (and other COVID-19 related health behaviors). What did the survey find? Basically, most people intend to engage in social distancing behaviors (e.g., avoiding large crowds) and other behaviors that reduce the spread of COVID-19 (e.g., washing hands at least 20 seconds). When most people intend to engage in a behavior, then public health professionals try to leverage that to move more people to act.
Now we need innovative and professional images that attempt to communicate one or all of these findings. The specific findings are nicely summarized in the attached document. For example, 82% of participants intend to engage in social distancing.
What sort of visual are we looking for? Our preference is for an original illustration (or set of illustrations). Our preference is for (creative and powerful illustrations, but we are also open to the creative and well-executed infographics.
We need these images fast . We will award monetary prizes to the 3 best designs. If we like more than that, then we might purchase more (e.g., in past contests, we have purchased as many as 30 designs).
What we will need:
(1) The illustrations must be original and we will need the photoshop and/or illustrator files for all artwork.
(2) You can illustrate all of the findings or just one of them. We need creative approaches that do a lucid job of bringing the data to life. Most people intend to engage in these behaviors. How to communicate that? Republicans and Democrats do not differ in their intentions; how to communicate that?
(3) The illustration should say, somewhere: "Based on a survey of 400 U.S. adults conducted March 20 - 24th, 2020."

U.S. Adults

• Original illustrations based on the findings of the survey (see attached document).

```html
<!DOCTYPE html>
<html lang="en">
<head>
<meta charset="utf-8">
<title>Percent of Americans intending to engage in social distancing</title>
<link rel="stylesheet" href="https://fonts.googleapis.com/css2?family=Anton&family=Gochi+Hand&family=Arimo:wght@400&family=PT+Sans:ital,wght@0,700;1,700&display=swap">
<style>
  :root {
    --teal: #31c1aa;
    --teal-dark: #124a40;
    --yellow: #fde57a;
    --ink: #111111;
    --blue: #065685;
    --red: #d2404b;
    --track: #d1d2d4;
    --white: #ffffff;
    --paper: #ffffff;
  }
  * { box-sizing: border-box; margin: 0; padding: 0; }
  html, body { width: 1200px; height: 928px; overflow: hidden; background: var(--paper); }
  .infographic { position: relative; width: 1200px; height: 928px; }

  .header {
    position: absolute; left: 32px; top: 15px; width: 1127px; height: 222px;
    background: var(--teal); border-radius: 34px; text-align: center;
  }
  .header__title {
    position: absolute; left: 0; right: 0; top: 32px;
    font-family: "Anton", Impact, sans-serif; font-weight: 400; font-size: 39px; line-height: 1;
    color: var(--yellow); -webkit-text-stroke: 3px var(--ink); paint-order: stroke fill;
    letter-spacing: 0.2px;
  }
  .header__question {
    position: absolute; left: 0; right: 0; top: 106px;
    font-family: "Gochi Hand", cursive; font-size: 40px; line-height: 53px; color: var(--white);
  }

  .stat-bar {
    position: absolute; width: 330px; height: 92px; background: var(--track);
  }
  .stat-bar__fill {
    position: absolute; left: 0; top: 0; bottom: 0;
    display: flex; align-items: center; padding-left: 15px;
  }
  .stat-bar--blue .stat-bar__fill { background: var(--blue); }
  .stat-bar--red .stat-bar__fill { background: var(--red); }
  .stat-bar__value {
    flex: none; width: 78px; white-space: nowrap; overflow: visible;
  }
  .stat-bar__value span {
    display: inline-block; transform: scaleX(0.82); transform-origin: left center;
    font-family: "Anton", Impact, sans-serif; font-size: 38px; line-height: 1; color: var(--white);
    letter-spacing: -0.5px;
  }
  .stat-bar__label {
    font-family: "Arimo", Arial, sans-serif; font-size: 17px; line-height: 21px; color: var(--white);
    white-space: nowrap;
  }

  .icon {
    position: absolute; width: 140px; height: 92px; border-radius: 12px;
  }

  .summary__heading {
    position: absolute; left: 0; right: 0; top: 724px; text-align: center;
    font-family: "Anton", Impact, sans-serif; font-size: 54px; line-height: 1;
    color: var(--teal); -webkit-text-stroke: 2px var(--teal-dark); paint-order: stroke fill;
  }
  .summary__text {
    position: absolute; left: 0; right: 0; top: 793px; text-align: center;
    font-family: "PT Sans", "Myriad Pro", sans-serif; font-style: italic; font-weight: 700;
    font-size: 33px; line-height: 1; color: var(--ink);
  }

  .footnote {
    position: absolute; left: 31px; top: 851px; width: 1131px; height: 50px;
    background: var(--red); color: var(--white); text-align: center;
    font-family: "PT Sans", "Myriad Pro", sans-serif; font-weight: 700; font-size: 18px; line-height: 50px;
  }
</style>
</head>
<body>
<main class="infographic">
  <header class="header">
    <h1 class="header__title">Percent of Americans intending to engage in social distancing</h1>
    <p class="header__question">“We would like to know how likely it is that you will perform<br>these behaviors to slow the spread of coronavirus?”</p>
  </header>

  <div class="icon" style="left:85px;top:252px;background:linear-gradient(90deg,#cfeee6,#fff3c4,#ffe1bd)" role="img" aria-label="Two people standing apart with a double-headed arrow between them"></div>
  <div class="stat-bar stat-bar--blue" style="left:249px;top:252px">
    <div class="stat-bar__fill" style="width:81%"><span class="stat-bar__value"><span>81%</span></span><span class="stat-bar__label">intend to<br>Engage in social<br>distancing</span></div>
  </div>

  <div class="icon" style="left:110px;top:371px;background:linear-gradient(135deg,#d6effa,#e6e6e6)" role="img" aria-label="Person working on a laptop beside a window"></div>
  <div class="stat-bar stat-bar--red" style="left:249px;top:371px">
    <div class="stat-bar__fill" style="width:82%"><span class="stat-bar__value"><span>82%</span></span><span class="stat-bar__label">intend to<br>Work from Home</span></div>
  </div>

  <div class="icon" style="left:85px;top:489px;background:linear-gradient(90deg,#fbd3d6,#c9d4dd)" role="img" aria-label="Person turning away from a large crowd"></div>
  <div class="stat-bar stat-bar--blue" style="left:249px;top:489px">
    <div class="stat-bar__fill" style="width:63%"><span class="stat-bar__value"><span>63%</span></span><span class="stat-bar__label">intend to<br>Avoid large<br>gatherings</span></div>
  </div>

  <div class="icon" style="left:105px;top:608px;width:112px;border-radius:50%;background:radial-gradient(circle,#f3f3f3 55%,#f3c7ca)" role="img" aria-label="Crossed-out sign over party items"></div>
  <div class="stat-bar stat-bar--red" style="left:249px;top:608px">
    <div class="stat-bar__fill" style="width:85%"><span class="stat-bar__value"><span>85%</span></span><span class="stat-bar__label">intend to<br>Cancel social activities</span></div>
  </div>

  <div class="icon" style="left:605px;top:252px;background:linear-gradient(90deg,#ffe7c2,#fff3c4,#cfeee6)" role="img" aria-label="Two small figures separated by a measuring ruler"></div>
  <div class="stat-bar stat-bar--blue" style="left:757px;top:252px">
    <div class="stat-bar__fill" style="width:81%"><span class="stat-bar__value"><span>81%</span></span><span class="stat-bar__label">intend to<br>Put distance between<br>yourself and other<br>people</span></div>
  </div>

  <div class="icon" style="left:615px;top:366px;height:104px;background:linear-gradient(135deg,#fff3c4,#d9f3fb)" role="img" aria-label="Person washing hands next to a timer"></div>
  <div class="stat-bar stat-bar--red" style="left:757px;top:371px">
    <div class="stat-bar__fill" style="width:85%"><span class="stat-bar__value"><span>85%</span></span><span class="stat-bar__label">intend to<br>Wash hands at least<br>20 seconds</span></div>
  </div>

  <div class="icon" style="left:640px;top:494px;width:95px;height:95px;background:linear-gradient(135deg,#d6edf8,#dcefc8)" role="img" aria-label="Hand sanitizer bottle with a check mark"></div>
  <div class="stat-bar stat-bar--blue" style="left:757px;top:489px">
    <div class="stat-bar__fill" style="width:87%"><span class="stat-bar__value"><span>87%</span></span><span class="stat-bar__label">intend to<br>Use hand sanitizer</span></div>
  </div>

  <div class="icon" style="left:620px;top:608px;height:100px;background:linear-gradient(90deg,#cfeee6,#f6c9cc)" role="img" aria-label="Person touching their face next to a red cross mark"></div>
  <div class="stat-bar stat-bar--red" style="left:757px;top:608px">
    <div class="stat-bar__fill" style="width:85%"><span class="stat-bar__value"><span>85%</span></span><span class="stat-bar__label">intend to<br>Avoid touching your<br>eyes, nose, and mouth</span></div>
  </div>

  <section class="summary">
    <h2 class="summary__heading">What does this data say?</h2>
    <p class="summary__text">It says that most people intend to engage in these behaviors.</p>
  </section>

  <footer class="footnote">Based on a survey of 400 U.S. adults conducted March 20 - 24th, 2020.</footer>
</main>
</body>
</html>
```